New Website for World Wide Charity (KOLVAN)

We need a dynamic web design for our brand new charity organisation that will be working worldwide. We will be funded by donations so need to attract people to donate.

What We Do
We work to optimise the wellbeing of the planet, the animals and all that live within. Our slogan is Achieving Vibrational Equilibrium.

We have included a Powerpoint document which may help you understand what we need, it is just an idea for structure and style, it is not set in stone so feel free to be as creative as you like!
Updates

Designs look the same

Target Market(s)

Adults 18+ with an interest in animal, environmental. Businesses that may like to support our natural world or already support our natural world.

Number of Pages Required

3 page

Colors

Designer to choose colors to be used in the design.

Requirements
Must have
• We need the website to be easy to use and understand.

Web pages will be Home, What We Do, Who We Are, Success Stories, What You Can Do (Blog section), Seek Help, Donate, Join.
Nice to have
• Natural feel, easy to navigate, Ideally the website will look natural and organic.

Natural colours, blues, greens, sand, gold, brown, grey, silver, Orange and yellow for impact.
Should not have
• Should not have a dark coloured theme.

```html
<!DOCTYPE html>
<html lang="en">
<head>
<meta charset="utf-8">
<title>KOLVAN – Help Raise World Vibration</title>
<link href="https://fonts.googleapis.com/css2?family=Arimo:wght@400;700&display=swap" rel="stylesheet">
<style>
:root{
  --blue:#6580b9;
  --blue-deep:#3f5ea8;
  --blue-dark:#2c4a8f;
  --ink:#1f2a44;
  --white:#ffffff;
  --snow:#e7ebf2;
  --pink:#d9c8dc;
}
*{margin:0;padding:0;box-sizing:border-box}
html,body{width:1200px;height:2902px;overflow:hidden;background:var(--white)}
body{font-family:"Arimo",Arial,sans-serif;position:relative;color:var(--ink)}
.abs{position:absolute}

/* hero */
.hero-bg{left:0;top:0;width:1200px;height:880px;
  background:linear-gradient(180deg,#9aa9c3 0%,#c3ccda 18%,#b5bdc9 32%,#dfe3ea 55%,#c8ccd3 75%,#d6d9de 100%)}
.hero-curve{left:0;top:600px}
.nav a{position:absolute;top:53px;font-size:14px;font-weight:700;color:#2a2f3d;text-decoration:none;letter-spacing:.2px}
.nav .active{border-bottom:3px solid var(--blue);padding-bottom:6px}
.brand{width:156px;height:156px;border-radius:50%;border:2px solid var(--blue);background:rgba(255,255,255,.55);
  display:flex;align-items:center;justify-content:center;font-size:20px;color:var(--blue-deep)}
.hero-title{left:0;width:1200px;top:252px;text-align:center;font-size:54px;font-weight:700;color:var(--white);
  text-shadow:0 2px 6px rgba(0,0,0,.45)}
.btn{display:flex;align-items:center;justify-content:center;border-radius:26px;background:var(--blue);
  color:var(--white);font-weight:700;font-size:15px}
.hero-btn{left:498px;top:330px;width:206px;height:50px;box-shadow:0 3px 8px rgba(0,0,0,.2)}

.cat{border-radius:50%;display:flex;flex-direction:column;align-items:center;justify-content:center;
  color:var(--white);font-weight:700;box-shadow:0 6px 16px rgba(0,0,0,.25)}
.cat-env{left:136px;top:536px;width:272px;height:272px;font-size:27px;
  background:radial-gradient(circle at 50% 40%,#5f8a78,#3f6190 70%)}
.cat-hum{left:787px;top:536px;width:272px;height:272px;font-size:33px;
  background:radial-gradient(circle at 50% 40%,#3c66b0,#1c3778 75%)}
.cat-ani{left:414px;top:486px;width:372px;height:372px;
  background:radial-gradient(circle at 50% 40%,#6f8ccb,#2f5099 80%)}
.cat-ani .ring{position:absolute;left:18px;top:18px;width:336px;height:336px;border-radius:50%;border:2px solid var(--pink)}
.cat-ani h2{font-size:36px;margin-top:-30px}
.cat-ani .btn{margin-top:48px;width:178px;height:48px;background:rgba(117,142,200,.95);position:relative}
.chev{width:20px;height:20px;border-radius:50%;background:var(--white);margin-top:50px;display:flex;align-items:center;justify-content:center}
.cat-env span,.cat-hum span{margin-top:50px}

/* features */
.photo{border-radius:16px;overflow:hidden;box-shadow:0 4px 12px rgba(0,0,0,.18)}
.photo .frame{position:absolute;left:20px;top:20px;right:20px;bottom:20px;border:2px solid var(--pink);border-radius:14px}
.panel{background:var(--blue);color:var(--white)}
.panel h2{position:absolute;font-size:40px;font-weight:700}
.panel .rule{position:absolute;width:75px;height:4px;background:var(--white)}
.panel p{position:absolute;width:427px;font-size:14.5px;line-height:22.4px;text-align:justify}

/* footer */
.foot-bg{left:0;top:2300px;width:1200px;height:602px;
  background:linear-gradient(180deg,#3f72c6 0%,#7aa4dc 25%,#c6d4e8 45%,#e9eef5 65%,#d5deeb 100%)}
.foot-card{top:2552px;height:266px;background:rgba(101,128,185,.82);border-radius:14px;color:var(--white)}
.foot-card h3{position:absolute;left:46px;top:48px;font-size:21px;font-weight:700}
.foot-card ul{position:absolute;left:46px;top:106px;list-style:none}
.foot-card li{font-size:15px;height:35.5px}
.foot-card li::before{content:"»";margin-right:14px}
.copy{left:0;width:1200px;top:2852px;text-align:center;font-size:14px;color:var(--white)}
</style>
</head>
<body>

<header>
  <div class="abs hero-bg" role="img" aria-label="Snowy mountain landscape with pine trees"></div>
  <svg class="abs hero-curve" width="1200" height="280" viewBox="0 0 1200 280">
    <path d="M0 170 Q600 -60 1200 170 L1200 280 L0 280 Z" fill="#ffffff"/>
  </svg>
  <nav class="nav">
    <a class="active" style="left:110px">HOME</a>
    <a style="left:174px">WHAT WE DO</a>
    <a style="left:288px">SUCCESS STORIES</a>
    <a style="left:709px">WHO WE ARE</a>
    <a style="left:823px">WHAT YOU CAN DO</a>
    <a style="left:978px">DONATE</a>
    <a style="left:1058px">JOIN</a>
  </nav>
  <div class="abs brand" style="left:496px;top:14px">KOLVAN</div>
  <h1 class="abs hero-title">HELP RAISE WORLD VIBRATION</h1>
  <a class="abs btn hero-btn">MAKE A DIFFERENCE</a>

  <div class="abs cat cat-env" role="img" aria-label="Environment: hands holding a tree">
    <span>ENVIRONMENT</span>
    <div class="chev"><svg width="10" height="10" viewBox="0 0 10 10"><path d="M3 1 L7 5 L3 9" stroke="#2c4a8f" stroke-width="2" fill="none"/></svg></div>
  </div>
  <div class="abs cat cat-ani" role="img" aria-label="Animal: polar bear on ice">
    <div class="ring"></div>
    <h2>ANIMAL</h2>
    <a class="btn">FIND OUT MORE</a>
  </div>
  <div class="abs cat cat-hum" role="img" aria-label="Human: connected network of people">
    <span>HUMAN</span>
    <div class="chev"><svg width="10" height="10" viewBox="0 0 10 10"><path d="M3 1 L7 5 L3 9" stroke="#2c4a8f" stroke-width="2" fill="none"/></svg></div>
  </div>
</header>

<main>
  <section>
    <div class="abs panel" style="left:560px;top:953px;width:528px;height:354px;border-radius:0 16px 16px 0">
      <h2 style="left:56px;top:60px">ENVIRONMENT</h2>
      <div class="rule" style="left:58px;top:108px"></div>
      <p style="left:58px;top:134px">Lorem ipsum dolor sit amet, consectetur adipiscing elit, sed do eiusmod tempor incididunt ut labore et dolore magna aliqua. Ut enim ad minim veniam, quis nostrud exercitation ullamco laboris nisi ut aliquip ex ea commodo consequat. Duis aute irure dolor in reprehenderit in voluptate velit esse cillum dolore eu fugiat nulla pariatur. Excepteur sint occaecat cupidatat non proident, sunt in culpa qui officia deserunt mollit anim id est laborum.</p>
    </div>
    <div class="abs photo" style="left:112px;top:906px;width:470px;height:449px;background:linear-gradient(180deg,#1f3552 0%,#4a5e7e 45%,#b6b4c4 65%,#eef0f6 100%)" role="img" aria-label="Snow-covered log cabin under a starry night sky"><div class="frame"></div></div>
  </section>

  <section>
    <div class="abs panel" style="left:112px;top:1403px;width:530px;height:355px;border-radius:16px 0 0 16px">
      <h2 style="left:40px;top:60px">ANIMAL</h2>
      <div class="rule" style="left:42px;top:108px"></div>
      <p style="left:43px;top:134px">Lorem ipsum dolor sit amet, consectetur adipiscing elit, sed do eiusmod tempor incididunt ut labore et dolore magna aliqua. Ut enim ad minim veniam, quis nostrud exercitation ullamco laboris nisi ut aliquip ex ea commodo consequat. Duis aute irure dolor in reprehenderit in voluptate velit esse cillum dolore eu fugiat nulla pariatur. Excepteur sint occaecat cupidatat non proident, sunt in culpa qui officia deserunt mollit anim id est laborum.</p>
    </div>
    <div class="abs photo" style="left:617px;top:1357px;width:471px;height:449px;background:linear-gradient(180deg,#9fb0bf 0%,#dfe6ec 45%,#f1f3f5 65%,#aab9c6 100%)" role="img" aria-label="Polar bear standing on an ice floe"><div class="frame"></div></div>
  </section>

  <section>
    <div class="abs panel" style="left:560px;top:1855px;width:528px;height:354px;border-radius:0 16px 16px 0">
      <h2 style="left:56px;top:60px">HUMAN</h2>
      <div class="rule" style="left:58px;top:108px"></div>
      <p style="left:58px;top:134px">Lorem ipsum dolor sit amet, consectetur adipiscing elit, sed do eiusmod tempor incididunt ut labore et dolore magna aliqua. Ut enim ad minim veniam, quis nostrud exercitation ullamco laboris nisi ut aliquip ex ea commodo consequat. Duis aute irure dolor in reprehenderit in voluptate velit esse cillum dolore eu fugiat nulla pariatur. Excepteur sint occaecat cupidatat non proident, sunt in culpa qui officia deserunt mollit anim id est laborum.</p>
    </div>
    <div class="abs photo" style="left:112px;top:1808px;width:470px;height:450px;background:linear-gradient(160deg,#8a7a72 0%,#b79885 35%,#7f8f68 60%,#d0b7a8 100%)" role="img" aria-label="Circle of joined hands"><div class="frame"></div></div>
  </section>
</main>

<footer>
  <div class="abs foot-bg" role="img" aria-label="Snowy mountain range under a blue sky"></div>
  <svg class="abs" style="left:0;top:2290px" width="1200" height="180" viewBox="0 0 1200 180">
    <path d="M0 0 L1200 0 L1200 22 Q600 260 0 22 Z" fill="#ffffff"/>
  </svg>
  <div class="abs" style="left:500px;top:2328px;width:200px;height:200px;border-radius:50%;background:var(--white)"></div>
  <div class="abs brand" style="left:520px;top:2348px;width:160px;height:160px;background:#f4f1f6">KOLVAN</div>

  <div class="abs foot-card" style="left:110px;width:315px">
    <h3>Get Involved</h3>
    <ul><li>Join Us</li><li>Fundraise</li><li>Donate</li><li>Shop</li></ul>
  </div>
  <div class="abs foot-card" style="left:445px;width:313px">
    <h3>Get Help</h3>
    <ul><li>Contact Us</li><li>Media</li></ul>
  </div>
  <div class="abs foot-card" style="left:778px;width:312px">
    <h3>Legal</h3>
    <ul><li>Terms and Conditions</li><li>Cookies</li><li>Privacy Policy</li></ul>
  </div>
  <p class="abs copy">© Copyrights 2021 Company name | All Rights Reserved</p>
</footer>

</body>
</html>
```